KV HOLDING Business Cards

I need business cards for "KV Holding group LLC" doublesided... logo on the back (also include logo on front)
logo attached to project... i have jpg up..
Company Info:
827 North Cadwell Avenue, Suite 4B
Chicago, Illinois 60654
facsimile 312-481-2075 (list fax, address, website on all cards.)
www.kvholdinggroup.example
Three different people on cards:
Darnell P. Okafor, CPA MST
Principal
ofc 312-481-3900
mobile 312-204-7751
darnellpokafor@kvholdinggroup.example
Hollis T. Brennecke, CPA MST
Principal
hollistbrennecke@kvholdinggroup.example
mobile 708-539-1184
ofc 312-481-3900
Conrad M Pavlik
Principal
ofc 312-481-3900
no mobile
conradmpavlik@kvholdinggroup.example
I have multiple projects listed.. see below:
Business cards for amber gate ventures llc
letterhead
envelopes
Business cards for KV Holding LLC
letterhead
envelopes
Target Market(s)
rich people
Industry/Entity Type
Business
Look and feel
Each slider illustrates characteristics of the customer's brand and the style your logo design should communicate.

```html
<!DOCTYPE html>
<html lang="en">
<head>
<meta charset="utf-8">
<title>KV Holding Group LLC – Business Cards</title>
<link rel="stylesheet" href="https://fonts.googleapis.com/css2?family=Cinzel:wght@400&family=Roboto:wght@400&display=swap">
<style>
  :root {
    --navy: #173f6e;
    --card-grey: #c4c4c4;
    --card-white: #ffffff;
    --backdrop: #383838;
    --panel-text: #ffffff;
  }
  * { margin: 0; padding: 0; box-sizing: border-box; }
  html, body { width: 1200px; height: 1000px; overflow: hidden; }
  body { background: var(--backdrop); position: relative; font-family: "Roboto", Arial, sans-serif; }

  .card { position: absolute; width: 500px; height: 292px; }
  .card--back { left: 77px; background: var(--card-grey); }
  .card--front { left: 631px; background: var(--card-white); }
  .row-1 { top: 31px; }
  .row-2 { top: 348px; }
  .row-3 { top: 668px; }

  .brand-name {
    font-family: "Cinzel", Georgia, serif;
    font-weight: 400;
    color: var(--navy);
    text-align: center;
    white-space: nowrap;
  }
  .card--back .brand-name {
    position: absolute; left: 0; right: 0; top: 182px;
    font-size: 33px; letter-spacing: 0.5px;
  }
  .brand-name .suffix { font-size: 0.55em; letter-spacing: 1px; }
  .card--back .website {
    position: absolute; left: 0; right: 0; top: 225px;
    font-family: "Cinzel", Georgia, serif; text-transform: lowercase;
    font-size: 20px; letter-spacing: 2.4px; color: var(--navy); text-align: center;
  }
  .card--back .brand-mark {
    position: absolute; left: 226px; top: 90px; width: 48px; height: 48px;
    border-radius: 50%; background: var(--navy);
  }

  .card--front .brand-name {
    position: absolute; left: 0; right: 0; top: 92px; font-size: 17px;
  }
  .card--front .brand-mark {
    position: absolute; left: 236px; top: 50px; width: 28px; height: 28px;
    border-radius: 50%; background: var(--navy);
  }

  .contact-panel {
    position: absolute; left: 30px; right: 30px; top: 129px; bottom: 0;
    background: var(--navy); color: var(--panel-text); text-align: center;
  }
  .person-name { margin-top: 11px; font-size: 19px; line-height: 22px; }
  .person-title { font-size: 12px; line-height: 15px; }
  .contact-lines { margin-top: 10px; list-style: none; font-size: 11px; line-height: 14px; }
  .company-footer {
    position: absolute; left: 0; right: 0; bottom: 15px;
    font-size: 10.5px; white-space: nowrap;
  }
</style>
</head>
<body>

  <!-- Backs -->
  <section class="card card--back row-1">
    <span class="brand-mark"></span>
    <p class="brand-name">KV Holding Group <span class="suffix">LLC</span></p>
    <p class="website">www.kvholdinggroup.example</p>
  </section>
  <section class="card card--back row-2">
    <span class="brand-mark"></span>
    <p class="brand-name">KV Holding Group <span class="suffix">LLC</span></p>
    <p class="website">www.kvholdinggroup.example</p>
  </section>
  <section class="card card--back row-3">
    <span class="brand-mark"></span>
    <p class="brand-name">KV Holding Group <span class="suffix">LLC</span></p>
    <p class="website">www.kvholdinggroup.example</p>
  </section>

  <!-- Fronts -->
  <section class="card card--front row-1">
    <span class="brand-mark"></span>
    <p class="brand-name">KV Holding Group <span class="suffix">LLC</span></p>
    <div class="contact-panel">
      <h2 class="person-name">Darnell P. Okafor, CPA MST</h2>
      <p class="person-title">Principal</p>
      <ul class="contact-lines">
        <li>Office : 312-481-3900</li>
        <li>Direct : 312-481-3912</li>
        <li>Mobile : 312-204-7751</li>
        <li>Facsimile : 312-481-2075</li>
        <li>Email : darnellpokafor@kvholdinggroup.example</li>
      </ul>
      <p class="company-footer">827 North Cadwell Avenue, Suite 4B Chicago, Illinois 60654 | www.kvholdinggroup.example</p>
    </div>
  </section>

  <section class="card card--front row-2">
    <span class="brand-mark"></span>
    <p class="brand-name">KV Holding Group <span class="suffix">LLC</span></p>
    <div class="contact-panel">
      <h2 class="person-name">Hollis T. Brennecke, CPA MST</h2>
      <p class="person-title">Principal</p>
      <ul class="contact-lines">
        <li>Office : 312-481-3900</li>
        <li>Mobile : 708-539-1184</li>
        <li>Facsimile : 312-481-2075</li>
        <li>Email : hollistbrennecke@kvholdinggroup.example</li>
      </ul>
      <p class="company-footer">827 North Cadwell Avenue, Suite 4B Chicago, Illinois 60654 | www.kvholdinggroup.example</p>
    </div>
  </section>

  <section class="card card--front row-3">
    <span class="brand-mark"></span>
    <p class="brand-name">KV Holding Group <span class="suffix">LLC</span></p>
    <div class="contact-panel">
      <h2 class="person-name">Conrad M Pavlik</h2>
      <p class="person-title">Principal</p>
      <ul class="contact-lines" style="margin-top:16px">
        <li>Office : 312-481-3900</li>
        <li>Facsimile : 312-481-2075</li>
        <li>Email : conradmpavlik@kvholdinggroup.example</li>
      </ul>
      <p class="company-footer">827 North Cadwell Avenue, Suite 4B Chicago, Illinois 60654 | www.kvholdinggroup.example</p>
    </div>
  </section>

</body>
</html>
```